Business card design

We need a business card designed completed for a new company. We are a company that works with associations, schools to convert their older text/DVDs into dynamic online and mobile programs. Our initial platform is designed for the legal associations and will enable their lawyers to access their content such as forms, videos, case law and support materials anywhere, anytime. We are also focused on Project Management Associations, Financial Management Associations and IT Associations.

I would like for the business card to have the following information:

Logo

Kent marrowby

President and CEO

kmarrowby@trevantiq.example

Mobile: 555-374-9160

www.trevantiq.example

Tag line: Transforming content into a mobile platform    

I would like it to be double sided, use the colours of the logo, tie into the mobile world

 

Industry/Entity Type

Legal

Logo Text

Trevantiq

```html
<!DOCTYPE html>
<html lang="en">
<head>
<meta charset="utf-8">
<title>Trevantiq business card</title>
<link rel="stylesheet" href="https://fonts.googleapis.com/css2?family=PT+Sans:wght@400;700&display=swap">
<style>
  :root {
    --backdrop: #6a4a31;
    --label: #1f1510;
    --card-grey: #989898;
    --card-white: #ffffff;
    --band-dark: #626262;
    --swoosh-mid: #a2a2a2;
    --ink-dark: #4a4a4a;
    --ink-logo-dark: #5a5a5a;
    --ink-light: #ffffff;
  }
  html, body {
    margin: 0;
    width: 1200px;
    height: 800px;
    overflow: hidden;
  }
  body {
    position: relative;
    background: var(--backdrop);
    font-family: "PT Sans", "Myriad Pro", Arial, sans-serif;
  }
  .side-label {
    position: absolute;
    width: 200px;
    margin-left: -100px;
    text-align: center;
    font-size: 21px;
    color: var(--label);
  }
  .card {
    position: absolute;
    width: 510px;
    height: 290px;
    border-radius: 22px;
    overflow: hidden;
    box-shadow: 0 6px 14px rgba(0,0,0,0.45);
  }
  .card--grey { background: var(--card-grey); }
  .card--white { background: var(--card-white); }
  .card__swoosh {
    position: absolute;
    inset: 0;
    width: 510px;
    height: 290px;
  }
  .logo-name {
    position: absolute;
    margin: 0;
    font-weight: 700;
    line-height: 1;
    letter-spacing: -0.5px;
  }
  .card--grey .logo-name { color: var(--ink-light); }
  .card--white .logo-name { color: var(--ink-logo-dark); }
  .logo-name--small { left: 26px; top: 36px; font-size: 52px; }
  .logo-name--large { left: 0; right: 0; top: 98px; text-align: center; font-size: 84px; }
  .contact {
    position: absolute;
    left: 26px;
    top: 140px;
    color: var(--ink-dark);
    font-size: 13px;
  }
  .contact__name { margin: 0 0 9px; font-size: 15px; font-weight: 700; }
  .contact__role { font-size: 13px; font-weight: 400; }
  .contact__line { margin: 0 0 8px; }
  .contact__key { font-weight: 700; font-style: italic; }
  .tagline {
    position: absolute;
    right: 27px;
    top: 243px;
    margin: 0;
    text-align: right;
    color: var(--ink-light);
    font-size: 15px;
    line-height: 19px;
  }
  .web-address {
    position: absolute;
    left: 0;
    right: 0;
    top: 253px;
    margin: 0;
    text-align: center;
    font-size: 16px;
    letter-spacing: 3px;
    color: #222;
  }
</style>
</head>
<body>

  <div class="side-label" style="left:330px; top:50px;">Front</div>
  <div class="side-label" style="left:888px; top:50px;">Back - 1</div>
  <div class="side-label" style="left:330px; top:410px;">Back - 2</div>
  <div class="side-label" style="left:888px; top:410px;">Back - 3</div>

  <!-- Front -->
  <section class="card card--grey" style="left:80px; top:97px;">
    <svg class="card__swoosh" viewBox="0 0 510 290" aria-hidden="true">
      <path d="M0,262 Q300,250 510,112 L510,150 Q330,256 0,268 Z" fill="#ffffff"/>
      <path d="M0,274 Q320,266 510,152 L510,290 L0,290 Z" fill="var(--band-dark)"/>
    </svg>
    <p class="logo-name logo-name--small">Trevantiq</p>
    <div class="contact">
      <p class="contact__name">Kent marrowby, <span class="contact__role">President and CEO</span></p>
      <p class="contact__line"><span class="contact__key">C</span> : 555-374-9160</p>
      <p class="contact__line"><span class="contact__key">E</span> : kmarrowby@trevantiq.example</p>
      <p class="contact__line"><span class="contact__key">W</span> : www.trevantiq.example</p>
    </div>
    <p class="tagline">Transforming content<br>into a mobile platform</p>
  </section>

  <!-- Back 1 -->
  <section class="card card--white" style="left:638px; top:97px;">
    <svg class="card__swoosh" viewBox="0 0 510 290" aria-hidden="true">
      <path d="M0,258 Q300,244 510,108 L510,142 Q320,252 0,266 Z" fill="var(--swoosh-mid)"/>
      <path d="M0,268 Q325,258 510,144 L510,150 Q330,264 0,272 Z" fill="var(--band-dark)"/>
      <path d="M0,275 Q330,266 510,154 L510,290 L0,290 Z" fill="var(--band-dark)"/>
    </svg>
    <p class="logo-name logo-name--small">Trevantiq</p>
    <div class="contact">
      <p class="contact__name">Kent marrowby, <span class="contact__role">President and CEO</span></p>
      <p class="contact__line"><span class="contact__key">C</span> : 555-374-9160</p>
      <p class="contact__line"><span class="contact__key">E</span> : kmarrowby@trevantiq.example</p>
      <p class="contact__line"><span class="contact__key">W</span> : www.trevantiq.example</p>
    </div>
    <p class="tagline">Transforming content<br>into a mobile platform</p>
  </section>

  <!-- Back 2 -->
  <section class="card card--grey" style="left:73px; top:452px;">
    <p class="logo-name logo-name--large">Trevantiq</p>
    <p class="web-address">www.trevantiq.example</p>
  </section>

  <!-- Back 3 -->
  <section class="card card--white" style="left:634px; top:450px;">
    <p class="logo-name logo-name--large">Trevantiq</p>
    <p class="web-address">www.trevantiq.example</p>
  </section>

</body>
</html>
```